New Flyer Design Project - for sale units at The Lodge phase 3

on attached the A2 is full kitchen 1 bedroom, the A3 is gally kitchen and the B2 is the the 2 bedroom, on attached pictures the room with 2 queen beds is only for the 2 bedroom

This is going to be used to sale the units (real estate sale) so the layout could possibly be text and then pictures maybe 1 bedroom on one side and 2 on the back?

Experience the Modern Luxury of the New Phase 3 Building of the
Lodge at Harper's Landing

* Opening Spring 2019

* America's #17 Family Resort; Tennessee's Only Ranked Resort

1 Bedroom Bunk Suite (Galley Kitchen) - $199,000; Sleeps 6

* Private King Master Bedroom

* Bunk Bed Galley

* Granite Counters Throughout

* Fully Furnished with Custom Furnishings

* Private Balcony

* Equipped Galley Kitchen

* In Unit Laundry

* Queen Sleeper Sofa

1 Bedroom Bunk Suite (Full Kitchen) - $209,000; Sleeps 6

* Bunk Bed Galley

* Granite Counters throughout

* Equipped Full Kitchen

* Completely Furnished with Custom Furnishings

* Private Balcony

* In Unit Laundry

* Queen Sleeper Sofa

2 Bedroom Bunk Suite (Full Kitchen) - $249,000; Sleeps 10

* Private King Master Bedroom with On-Suite Bathroom

* Two Queen Bedroom

* Bunk Bed Galley

* Full Kitchen

* Private Balcony

* In Unit Laundry

* Queen Sleeper Sofa

Target Market(s)

people wanting to buy units in phase 3 of The Lodge at governor's crossing

Industry/Entity Type

Real Estate Development

Requirements
Must have
• attached text to describe units and price
• pictures and layouts
• Contact Dale Fenton
• 865-555-0172 Dale@bluecedarretreats.example
Nice to have
• brand and logo
Should not have
• it should not be plain this is m ore of a luxury project

```html
<!DOCTYPE html>
<html lang="en">
<head>
<meta charset="utf-8">
<title>The Lodge at Harper's Landing – Phase 3 Flyer</title>
<link rel="stylesheet" href="https://fonts.googleapis.com/css2?family=Barlow:wght@400;500;600&family=Barlow+Semi+Condensed:wght@400;500&family=Lato:wght@400;700&family=Lobster+Two:ital,wght@1,700&display=swap">
<style>
  :root{
    --backdrop:#c9cacc;
    --sand:#d9a05a;
    --sand-dark:#b07d40;
    --bark:#6e5440;
    --bark-dark:#5a4332;
    --slate:#5a8290;
    --slate-dark:#456874;
    --cream:#f3e7d3;
    --teal-text:#3f7e82;
    --green-text:#4c8a2e;
    --ink:#2e2e2e;
    --white:#ffffff;
  }
  *{box-sizing:border-box;margin:0;padding:0}
  html,body{width:1200px;height:805px;overflow:hidden}
  body{background:var(--backdrop);position:relative;font-family:"Barlow",sans-serif}
  .page{position:absolute;top:48px;width:548px;height:709px;overflow:hidden}
  .page--front{left:38px;background:var(--white)}
  .page--back{left:614px}

  /* front */
  .hero-photo{position:absolute;left:0;top:0;width:548px;height:390px;
    background:linear-gradient(160deg,#dfe3b8 0%,#b9bf8e 35%,#6e6a52 70%,#5d6064 100%)}
  .headline{position:absolute;left:52px;top:150px;width:444px;height:138px;
    background:rgba(40,40,40,.85);border:3px solid var(--white);
    display:flex;align-items:center;justify-content:center;text-align:center;
    font-family:"Barlow Semi Condensed",sans-serif;font-weight:400;color:var(--white);font-size:26.5px;line-height:33px}
  .gallery{position:absolute;left:12px;top:326px;width:523px;height:130px;background:var(--sand);
    display:flex;gap:6px;padding:7px 8px}
  .gallery-photo{flex:1 1 0;height:100%}
  .gallery-photo--bedroom{background:linear-gradient(135deg,#cfd3a8,#f4f4ee 60%,#6d6d60)}
  .gallery-photo--dining{background:linear-gradient(135deg,#a9b07c,#5b5044 60%,#7a847a)}
  .gallery-photo--kitchen{background:linear-gradient(135deg,#dcdcc8,#8a7a66 50%,#3e3e3e)}
  .gallery-photo--bunks{background:linear-gradient(135deg,#e0cfa8,#6a5a4a 55%,#b9b38a)}
  .opening{position:absolute;left:110px;top:456px;width:328px;height:48px;background:var(--bark);
    clip-path:polygon(0 0,100% 0,94% 100%,6% 100%);
    display:flex;align-items:center;justify-content:center;
    font-family:"Lobster Two",sans-serif;font-style:italic;font-weight:700;color:var(--sand);font-size:29px}
  .ranking{position:absolute;left:0;width:548px;top:516px;text-align:center;
    font-family:"Lobster Two",sans-serif;font-style:italic;font-weight:700;color:var(--teal-text);font-size:18px}
  .award{position:absolute;left:0;width:548px;top:542px;display:flex;align-items:center;justify-content:center;gap:6px;
    font-family:"Lobster Two",sans-serif;font-style:italic;font-weight:700;color:var(--green-text);font-size:18px}
  .award-badge{width:20px;height:20px;border-radius:50%;background:var(--ink)}
  .award-name{font-family:"Barlow",sans-serif;font-style:normal;font-weight:400;color:var(--ink);font-size:19px}
  .contact{position:absolute;left:0;top:576px;width:548px;height:133px;background:var(--bark);color:var(--white);font-family:"Lato",sans-serif}
  .contact-label{position:absolute;left:35px;top:20px;font-size:18px}
  .contact-name{position:absolute;left:35px;top:44px;font-size:23px;font-weight:700}
  .contact-email{position:absolute;left:35px;top:80px;font-size:17.5px}
  .brand{position:absolute;left:370px;top:30px;display:flex;align-items:center;gap:8px}
  .brand-mark{width:18px;height:18px;background:var(--sand)}
  .brand-name{font-family:"Barlow",sans-serif;font-weight:600;font-size:30px;color:var(--sand)}

  /* back */
  .unit{position:absolute;left:0;width:548px;height:236px;overflow:hidden}
  .unit--one{top:0;background:var(--sand)}
  .unit--two{top:236px;background:var(--bark)}
  .unit--three{top:472px;height:237px;background:var(--slate)}
  .unit-rail{position:absolute;left:0;top:0;width:98px;height:100%;clip-path:polygon(0 0,80% 0,100% 50%,80% 100%,0 100%)}
  .unit--one .unit-rail{background:var(--sand-dark)}
  .unit--two .unit-rail{background:var(--bark-dark)}
  .unit--three .unit-rail{background:var(--slate-dark)}
  .unit-number{position:absolute;left:14px;top:38px;font-family:"Barlow",sans-serif;font-weight:600;font-size:150px;line-height:1;opacity:.25;color:var(--white)}
  .floor-plan{position:absolute;left:106px;border:3px solid var(--white);
    background:linear-gradient(180deg,#d9d1c2,#c6bcaa);width:240px}
  .unit--one .floor-plan{top:30px;height:197px}
  .unit--two .floor-plan{top:12px;height:208px}
  .unit--three .floor-plan{top:14px;height:198px}
  .unit-info{position:absolute;left:364px;color:var(--cream)}
  .unit--one .unit-info{top:44px}
  .unit--two .unit-info{top:32px}
  .unit--three .unit-info{top:12px;color:var(--white)}
  .unit-title{font-family:"Barlow",sans-serif;font-weight:600;font-size:14.5px;line-height:17px;color:inherit}
  .unit-features{list-style:none;margin-top:4px;font-family:"Barlow Semi Condensed",sans-serif;font-size:11px;line-height:14px}
  .unit-features li::before{content:"• "}
  .unit-features .indent{padding-left:7px}
  .unit-features .indent::before{content:""}
</style>
</head>
<body>
  <section class="page page--front">
    <div class="hero-photo" role="img" aria-label="Rendered suite bedroom with king bed, lamps and green curtains"></div>
    <h1 class="headline">Experience the Modern Luxury of the<br>New Phase 3 Building of the<br>Lodge at Harper's Landing</h1>
    <div class="gallery">
      <div class="gallery-photo gallery-photo--bedroom" role="img" aria-label="Queen bedroom"></div>
      <div class="gallery-photo gallery-photo--dining" role="img" aria-label="Living and dining area"></div>
      <div class="gallery-photo gallery-photo--kitchen" role="img" aria-label="Kitchen with granite island"></div>
      <div class="gallery-photo gallery-photo--bunks" role="img" aria-label="Bunk bed galley"></div>
    </div>
    <p class="opening">Opening Spring 2019</p>
    <p class="ranking">America's #17 Family Resort Tennessee's Only Ranked Resort</p>
    <p class="award"><span class="award-badge"></span><span class="award-name">TrailReview</span> Guests' Pick 2018</p>
    <footer class="contact">
      <p class="contact-label">Contact:</p>
      <p class="contact-name">Dale Fenton | 865-555-0172</p>
      <p class="contact-email">Dale@bluecedarretreats.example</p>
      <div class="brand"><span class="brand-mark"></span><span class="brand-name">The Lodge</span></div>
    </footer>
  </section>

  <section class="page page--back">
    <article class="unit unit--one">
      <div class="unit-rail"></div>
      <span class="unit-number">1</span>
      <div class="floor-plan" role="img" aria-label="Floor plan of 1 bedroom bunk suite with galley kitchen"></div>
      <div class="unit-info">
        <h2 class="unit-title">1 Bedroom Bunk Suite<br>(Galley Kitchen)<br>$199,000 : Sleeps 6</h2>
        <ul class="unit-features">
          <li>Private King Master Bedroom</li>
          <li>Bunk Bed Galley</li>
          <li>Granite Counters Throughout</li>
          <li>Fully Furnished with</li>
          <li class="indent">Custom Furnishings</li>
          <li>Private Balcony</li>
          <li>Equipped Galley Kitchen</li>
          <li>In Unit Laundry</li>
          <li>Queen Sleeper Sofa</li>
        </ul>
      </div>
    </article>
    <article class="unit unit--two">
      <div class="unit-rail"></div>
      <span class="unit-number">1</span>
      <div class="floor-plan" role="img" aria-label="Floor plan of 1 bedroom bunk suite with full kitchen"></div>
      <div class="unit-info">
        <h2 class="unit-title">1 Bedroom Bunk Suite<br>(Full Kitchen)<br>$209,000; Sleeps 6</h2>
        <ul class="unit-features">
          <li>Private King Master Bedroom</li>
          <li>Bunk Bed Galley</li>
          <li>Granite Counters throughout</li>
          <li>Equipped Full Kitchen</li>
          <li>Completely Furnished with</li>
          <li class="indent">Custom Furnishings</li>
          <li>Private Balcony</li>
          <li>In Unit Laundry</li>
          <li>Queen Sleeper Sofa</li>
        </ul>
      </div>
    </article>
    <article class="unit unit--three">
      <div class="unit-rail"></div>
      <span class="unit-number">2</span>
      <div class="floor-plan" role="img" aria-label="Floor plan of 2 bedroom bunk suite with full kitchen"></div>
      <div class="unit-info">
        <h2 class="unit-title">2 Bedroom Bunk Suite<br>(Full Kitchen)<br>$249,000; Sleeps 10</h2>
        <ul class="unit-features">
          <li>Private King Master Bedroom</li>
          <li class="indent">with On-Suite Bathroom</li>
          <li>Two Queen Bedroom</li>
          <li>Bunk Bed Galley</li>
          <li>Granite Counters Throughout</li>
          <li>Full Kitchen</li>
          <li>Completely Furnished with</li>
          <li class="indent">Custom Furnishings</li>
          <li>Private Balcony</li>
          <li>In Unit Laundry</li>
          <li>Queen Sleeper Sofa</li>
        </ul>
      </div>
    </article>
  </section>
</body>
</html>
```